eCommerce Website Design for Children's Book Service

I am looking for a 5 page eCommerce website that includes a Shopping Cart. 'Lumiva Books' is the title of the company and its logo is attached. 'Sprouting wonder in words,' is the company's motto and 'spring green' is the main color. The website needs to appeal to families. Images of books and/or maple seeds (helicopter seeds) moving are part of the graphics.
Updates

I have updated my brief and I would like my website design to include 5 pages: home, about, products (books), blog, contact. WordPress is the web format that I am most comfortable with.

Target Market(s)

Families with young children

Coding

Coded - Design and coding required

Number of Pages Required

5+ page

Requirements
Must have
• Shopping cart page; contact page, books page with spaces of photos to go, blog page; spring green color
Nice to have
• A graphic that relates to motto : "sprouting wonder in words"
• WordPress

```html
<!DOCTYPE html>
<html lang="en">
<head>
<meta charset="utf-8">
<title>Lumiva Books — Sprouting Wonder in Words</title>
<link href="https://fonts.googleapis.com/css2?family=Poppins:wght@400;500;600&family=Roboto:wght@500;700&display=swap" rel="stylesheet">
<style>
:root{
  --green:#3e9b3b;
  --green-dark:#2f8a2d;
  --ink:#111;
  --text:#555;
  --band:#333;
  --band-deep:#2b2b2b;
  --blue:#1a73c8;
  --white:#fff;
  --line:#ddd;
}
*{margin:0;padding:0;box-sizing:border-box}
html,body{width:1200px;height:4186px;overflow:hidden}
body{position:relative;background:var(--white);font-family:'Poppins',sans-serif;color:var(--text)}
.abs{position:absolute}
.btn{position:absolute;background:var(--green);color:var(--white);font:500 15px 'Poppins',sans-serif;display:flex;align-items:center;justify-content:center}
.h2{position:absolute;left:0;width:1200px;text-align:center;font:700 36px 'Roboto',sans-serif;color:var(--ink);letter-spacing:.5px}
.h2 span{color:var(--green)}
.lead{position:absolute;left:300px;width:600px;text-align:center;font:400 15px/34px 'Poppins',sans-serif;color:var(--text)}
/* header */
.brand{left:112px;top:14px;display:flex;flex-direction:column;align-items:center}
.brand-mark{width:40px;height:40px;background:var(--green);border-radius:50%}
.brand-name{font:500 20px 'Poppins',sans-serif;color:var(--green);margin-top:6px}
.signup{left:748px;top:17px;width:123px;height:45px;font-weight:600}
.login{left:886px;top:17px;width:124px;height:45px;background:var(--white);color:var(--green);border:3px solid var(--green);font-weight:600}
.nav{left:488px;top:86px;display:flex;gap:28px;font:600 15px 'Poppins',sans-serif;color:var(--ink)}
/* hero */
.hero{left:0;top:123px;width:1200px;height:555px;background:linear-gradient(90deg,#5a5140 0%,#8a7a5e 35%,#c9b79a 60%,#e8d7c3 78%,#a24a4f 100%)}
.hero-title{left:110px;top:298px;font:600 42px 'Poppins',sans-serif;color:var(--white)}
.hero-text{left:110px;top:366px;width:500px;font:500 19px/30px 'Poppins',sans-serif;color:var(--white)}
.shop{left:110px;top:493px;width:152px;height:56px;font-weight:600}
/* product cards */
.card-img{position:absolute;width:230px;height:342px;border:1px solid var(--line)}
.badge{position:absolute;left:0;top:0;padding:3px 10px;background:var(--green-dark);color:var(--white);font:600 13px 'Poppins',sans-serif}
.card-title{position:absolute;font:600 19px 'Poppins',sans-serif;color:var(--ink)}
.price{position:absolute;font:600 21px 'Poppins',sans-serif;color:var(--blue)}
.desc{position:absolute;width:230px;font:400 16px/33px 'Poppins',sans-serif;color:var(--text)}
.cart{width:125px;height:43px;font-size:14px}
.arrow{position:absolute}
/* bands */
.band{left:0;width:1200px;background:var(--band)}
.feature{position:absolute;width:220px;text-align:center;font:600 19px 'Poppins',sans-serif;color:var(--green)}
.feature svg{display:block;margin:0 auto 22px}
.offer-title{left:0;width:1200px;top:2858px;text-align:center;font:700 34px 'Roboto',sans-serif;color:var(--white)}
.email{left:312px;top:2949px;width:441px;height:56px;background:var(--white);font:400 15px 'Poppins',sans-serif;color:#777;padding:18px 20px}
.submit{left:753px;top:2949px;width:134px;height:56px;font-weight:600}
/* blog */
.date{position:absolute;padding:4px 10px;background:rgba(0,0,0,.55);color:var(--white);font:600 16px 'Poppins',sans-serif}
.post-title{position:absolute;font:600 20px 'Poppins',sans-serif;color:var(--ink)}
.post-text{position:absolute;font:400 17px/33px 'Poppins',sans-serif;color:var(--text)}
.more{height:38px;padding:0 20px;font-size:15px}
/* footer */
.footer{left:0;top:3811px;width:1200px;height:375px;background:var(--band-deep)}
.f-head{position:absolute;top:3872px;font:600 19px 'Poppins',sans-serif;color:var(--white)}
.f-list{position:absolute;top:3922px;list-style:none;font:400 15px/33px 'Poppins',sans-serif;color:var(--white)}
.contact-row{position:absolute;left:112px;display:flex;gap:22px;font:400 15px/24px 'Poppins',sans-serif;color:var(--white)}
.social{left:916px;top:3940px;display:flex;gap:14px}
.social i{width:18px;height:18px;border-radius:50%;background:var(--white);display:block}
.copy{left:0;width:1200px;top:4136px;text-align:center;font:400 15px 'Poppins',sans-serif;color:var(--white)}
</style>
</head>
<body>

<header>
  <div class="abs brand"><span class="brand-mark"></span><span class="brand-name">Lumiva Books</span></div>
  <div class="btn signup">SIGNUP</div>
  <div class="btn login">LOGIN</div>
  <svg class="abs" style="left:1035px;top:28px" width="28" height="24" viewBox="0 0 28 24"><path d="M0 2h5l4 13h14l3-10H8" fill="none" stroke="#111" stroke-width="3"/><circle cx="11" cy="21" r="2.5" fill="#111"/><circle cx="21" cy="21" r="2.5" fill="#111"/></svg>
  <nav class="abs nav"><span>HOME</span><span>PRODUCT</span><span>PRICING</span><span>PARTNERS</span><span>BLOG</span><span>CONTACT</span></nav>
  <svg class="abs" style="left:1054px;top:87px" width="16" height="16" viewBox="0 0 16 16"><circle cx="6.5" cy="6.5" r="5" fill="none" stroke="#111" stroke-width="2.5"/><path d="M10 10l5 5" stroke="#111" stroke-width="2.5"/></svg>
</header>

<section>
  <div class="abs hero" role="img" aria-label="Photo of a smiling girl resting her arms on a stack of books"></div>
  <svg class="arrow" style="left:34px;top:385px" width="26" height="50" viewBox="0 0 26 50"><path d="M22 4L5 25l17 21" fill="none" stroke="#fff" stroke-width="5"/></svg>
  <svg class="arrow" style="left:1116px;top:385px" width="26" height="50" viewBox="0 0 26 50"><path d="M4 4l17 21L4 46" fill="none" stroke="#fff" stroke-width="5"/></svg>
  <h1 class="abs hero-title">SPROUTING WONDER IN WORDS</h1>
  <p class="abs hero-text">Sed ut perspiciatis unde omnis iste natus error sit voluptatem accusantium doloremque laudantium,</p>
  <div class="btn shop">SHOP NOW</div>
</section>

<section>
  <h2 class="h2" style="top:755px">FEATURE <span>PRODUCTS</span></h2>
  <p class="lead" style="top:826px">"At vero eos et accusamus et iusto odio dignissimos ducimus qui blanditiis praesentium voluptatum deleniti atque corrupti quos dolores et quas molestias excepturi sint occaecati</p>
  <svg class="arrow" style="left:64px;top:1100px" width="22" height="42" viewBox="0 0 22 42"><path d="M18 3L4 21l14 18" fill="none" stroke="#111" stroke-width="5"/></svg>
  <svg class="arrow" style="left:1110px;top:1100px" width="22" height="42" viewBox="0 0 22 42"><path d="M4 3l14 18L4 39" fill="none" stroke="#111" stroke-width="5"/></svg>

  <div class="card-img" style="left:112px;top:943px;background:linear-gradient(160deg,#3f8a3a,#e0a253 60%,#2e7a35)" role="img" aria-label="Cover illustration of an animal reading a book in the jungle"><span class="badge">Best Seller</span></div>
  <div class="card-img" style="left:357px;top:943px;background:linear-gradient(160deg,#e4f2d8,#5cab4b 60%,#b9dfa6)" role="img" aria-label="Cover illustration of a green cartoon dinosaur"><span class="badge">Best Seller</span></div>
  <div class="card-img" style="left:605px;top:943px;background:linear-gradient(180deg,#bfe3f5,#e7d77a 45%,#7bbd55)" role="img" aria-label="Cover illustration of children under a rainbow with a giant open book"></div>
  <div class="card-img" style="left:851px;top:943px;background:linear-gradient(180deg,#eaf1f3,#7aa95a 50%,#8a5b34)" role="img" aria-label="Cover illustration of forest animals around a tree"><span class="badge">Best Seller</span></div>

  <div class="card-title" style="left:112px;top:1308px">At vero eos et accu</div>
  <div class="card-title" style="left:357px;top:1308px">At vero eos et accu</div>
  <div class="card-title" style="left:605px;top:1308px">At vero eos et accu</div>
  <div class="card-title" style="left:851px;top:1308px">At vero eos et accu</div>
  <div class="price" style="left:112px;top:1349px">$40.00</div>
  <div class="price" style="left:357px;top:1349px">$50.00</div>
  <div class="price" style="left:605px;top:1349px">$55.00</div>
  <div class="price" style="left:851px;top:1349px">$60.00</div>
  <div class="btn cart" style="left:112px;top:1400px">Add to Cart</div>
  <div class="btn cart" style="left:357px;top:1400px">Add to Cart</div>
  <div class="btn cart" style="left:605px;top:1400px">Add to Cart</div>
  <div class="btn cart" style="left:851px;top:1400px">Add to Cart</div>
</section>

<section>
  <div class="abs band" style="top:1537px;height:307px"></div>
  <div class="feature" style="left:119px;top:1622px">
    <svg width="92" height="92" viewBox="0 0 92 92"><circle cx="46" cy="46" r="46" fill="#fff"/><rect x="22" y="34" width="30" height="22" fill="#333"/><path d="M52 40h10l7 8v8H52z" fill="#333"/><circle cx="32" cy="60" r="5" fill="#333"/><circle cx="60" cy="60" r="5" fill="#333"/></svg>
    FREE SHIPPING</div>
  <div class="feature" style="left:367px;top:1622px">
    <svg width="92" height="92" viewBox="0 0 92 92"><circle cx="46" cy="46" r="46" fill="#fff"/><text x="46" y="60" text-anchor="middle" font-family="Poppins,sans-serif" font-size="42" font-weight="500" fill="#333">$</text></svg>
    MONEY GUARANTEE</div>
  <div class="feature" style="left:613px;top:1622px">
    <svg width="92" height="92" viewBox="0 0 92 92"><circle cx="46" cy="46" r="46" fill="#fff"/><circle cx="46" cy="46" r="26" fill="none" stroke="#333" stroke-width="4"/><path d="M46 28v18l10 6" fill="none" stroke="#333" stroke-width="3"/><text x="46" y="66" text-anchor="middle" font-family="Poppins,sans-serif" font-size="11" font-weight="600" fill="#333">24h</text></svg>
    STORE HOURS</div>
  <div class="feature" style="left:850px;top:1622px">
    <svg width="92" height="92" viewBox="0 0 92 92"><circle cx="46" cy="46" r="46" fill="#fff"/><circle cx="46" cy="40" r="12" fill="#333"/><path d="M26 70c2-12 10-16 20-16s18 4 20 16z" fill="#333"/><path d="M30 42a16 16 0 0132 0" fill="none" stroke="#333" stroke-width="3"/></svg>
    SUPPORT 24/7</div>
</section>

<section>
  <h2 class="h2" style="top:1920px">OUR <span>PRODUCTS</span></h2>
  <p class="lead" style="top:1991px">"At vero eos et accusamus et iusto odio dignissimos ducimus qui blanditiis praesentium voluptatum deleniti atque corrupti quos dolores et quas molestias excepturi sint occaecati</p>
  <svg class="arrow" style="left:64px;top:2272px" width="22" height="42" viewBox="0 0 22 42"><path d="M18 3L4 21l14 18" fill="none" stroke="#111" stroke-width="5"/></svg>
  <svg class="arrow" style="left:1110px;top:2272px" width="22" height="42" viewBox="0 0 22 42"><path d="M4 3l14 18L4 39" fill="none" stroke="#111" stroke-width="5"/></svg>

  <div class="card-img" style="left:112px;top:2109px;background:linear-gradient(180deg,#3c5a4a,#6f8a6a 55%,#2f4a3a)" role="img" aria-label="Illustration of a fairy tree house in a forest"></div>
  <div class="card-img" style="left:357px;top:2109px;background:linear-gradient(180deg,#a8c98a,#8a6a4a 55%,#b3cf8f)" role="img" aria-label="Illustration of a bear and a bird under a tree"></div>
  <div class="card-img" style="left:605px;top:2109px;background:linear-gradient(180deg,#a7c2d0,#8d9a56 45%,#8a6a3e)" role="img" aria-label="Illustration of hares in a field near a village"></div>
  <div class="card-img" style="left:851px;top:2109px;background:radial-gradient(circle at 50% 45%,#9a5fc4,#3b1a6a 60%,#1c0f3e)" role="img" aria-label="Illustration of a child reading a glowing magic book"></div>

  <div class="card-title" style="left:112px;top:2472px">At vero eos et accu</div>
  <div class="card-title" style="left:357px;top:2472px">At vero eos et accu</div>
  <div class="card-title" style="left:605px;top:2472px">At vero eos et accu</div>
  <div class="card-title" style="left:851px;top:2472px">At vero eos et accu</div>
  <div class="price" style="left:112px;top:2514px">$40.00</div>
  <div class="price" style="left:357px;top:2514px">$45.00</div>
  <div class="price" style="left:605px;top:2514px">$55.00</div>
  <div class="price" style="left:851px;top:2514px">$60.00</div>
  <p class="desc" style="left:112px;top:2558px">Nam libero tempore, cum soluta nobis est</p>
  <p class="desc" style="left:357px;top:2558px">Nam libero tempore, cum soluta nobis est</p>
  <p class="desc" style="left:605px;top:2558px">Nam libero tempore, cum soluta nobis est</p>
  <p class="desc" style="left:851px;top:2558px">Nam libero tempore, cum soluta nobis est</p>
  <div class="btn cart" style="left:112px;top:2650px">Add to Cart</div>
  <div class="btn cart" style="left:357px;top:2650px">Add to Cart</div>
  <div class="btn cart" style="left:605px;top:2650px">Add to Cart</div>
  <div class="btn cart" style="left:851px;top:2650px">Add to Cart</div>
</section>

<section>
  <div class="abs band" style="top:2787px;height:310px"></div>
  <h2 class="abs offer-title">GET SPECIAL OFFER IN YOUR INBOX</h2>
  <div class="abs email">Email</div>
  <div class="btn submit">Submit</div>
</section>

<section>
  <h2 class="h2" style="top:3160px">RECENT BLOG</h2>

  <div class="abs" style="left:112px;top:3264px;width:468px;height:279px;background:linear-gradient(135deg,#2a3a6a,#5a6fa8 45%,#c9b08a 75%,#6a5a4a)" role="img" aria-label="Photo of a mother reading to her children at bedtime"></div>
  <span class="date" style="left:112px;top:3276px">Sep 18</span>
  <div class="post-title" style="left:112px;top:3566px">Sed ut perspiciatis unde omnis</div>
  <p class="post-text" style="left:112px;top:3610px;width:470px">There are many variations of passages of Lorem Ipsum available, but the majority have suffered alteration in</p>
  <div class="btn more" style="left:112px;top:3683px">Read More</div>

  <div class="abs" style="left:614px;top:3264px;width:212px;height:212px;background:linear-gradient(160deg,#3a2a1e,#8a5a32 50%,#c08a4a)" role="img" aria-label="Photo of a child reading on a wooden floor"></div>
  <span class="date" style="left:614px;top:3276px">Oct 20</span>
  <div class="post-title" style="left:854px;top:3264px">Nemo enim ipsam</div>
  <p class="post-text" style="left:854px;top:3306px;width:236px">Contrary to popular belief, Lorem Ipsum is not simply random text. It has roots in</p>
  <div class="btn more" style="left:854px;top:3428px">Read More</div>

  <div class="abs" style="left:614px;top:3507px;width:212px;height:212px;background:linear-gradient(160deg,#e8e2d6,#d8b89a 50%,#6a9ac8)" role="img" aria-label="Photo of a toddler playing with a colourful toy"></div>
  <span class="date" style="left:614px;top:3519px">Feb 20</span>
  <div class="post-title" style="left:854px;top:3507px">Ipsum voluptatem</div>
  <p class="post-text" style="left:854px;top:3549px;width:236px">Contrary to popular belief, Lorem Ipsum is not simply random text. It has roots in</p>
  <div class="btn more" style="left:854px;top:3683px">Read More</div>
</section>

<footer>
  <div class="abs footer"></div>
  <div class="f-head" style="left:112px">Contact Us</div>
  <div class="contact-row" style="top:3926px">
    <svg width="14" height="20" viewBox="0 0 14 20"><path d="M7 0a7 7 0 00-7 7c0 5 7 13 7 13s7-8 7-13a7 7 0 00-7-7z" fill="#fff"/><circle cx="7" cy="7" r="2.5" fill="#2b2b2b"/></svg>
    <span>At vero eos et accusamus<br>et iusto odio</span></div>
  <div class="contact-row" style="top:3990px">
    <svg width="16" height="16" viewBox="0 0 16 16"><path d="M3 0l3 4-2 2c1 2 4 5 6 6l2-2 4 3-2 3C7 16 0 9 0 3z" fill="#fff"/></svg>
    <span>Phone 555 014 2200<br>Fax 555 014 7733</span></div>
  <div class="contact-row" style="top:4060px">
    <svg width="16" height="12" viewBox="0 0 16 12"><rect width="16" height="12" fill="#fff"/><path d="M0 0l8 7 8-7" fill="none" stroke="#2b2b2b" stroke-width="1.5"/></svg>
    <span>hello@lumivabooks.com</span></div>

  <div class="f-head" style="left:472px">Links</div>
  <ul class="f-list" style="left:472px;font-size:14px"><li>HOME</li><li>PRODUCT</li><li>PRICING</li><li>PARTNERS</li><li>BLOG</li></ul>

  <div class="f-head" style="left:662px">Support</div>
  <ul class="f-list" style="left:662px"><li>Terms &amp; Conditions</li><li>Privacy Policy</li><li>Returns</li><li>Site Map</li></ul>

  <div class="f-head" style="left:916px">Follow Us</div>
  <div class="abs social"><i></i><i></i><i></i><i></i></div>

  <p class="abs copy">Copy Rights © 2019 Lumiva Books All Rights Reserved.</p>
</footer>

</body>
</html>
```